QVR business card

Need a business card for a company that provides instructional design and elearning development services. The website is here: http://quorvane.studio/

I'm attaching a current logo, as well as the old business card design. While I like to keep it clean, the old design is too simplistic for my liking. The only idea I want to reuse from the old design is placing industry jargon on the back of the card, just need a better way to present it. But if you have other ideas for the back--feel free to experiment.

Please use the colors complementary to the color we have on the website. Thank you!

```html
<!DOCTYPE html>
<html lang="en">
<head>
<meta charset="utf-8">
<title>QVR business card</title>
<link rel="stylesheet" href="https://fonts.googleapis.com/css2?family=Open+Sans:wght@400;600;800&family=PT+Sans+Narrow:wght@400;700&display=swap">
<style>
  :root {
    --teal: #1db3ae;
    --teal-deep: #179d98;
    --gold: #d9c98f;
    --ink: #2b3a3a;
    --paper: #ffffff;
    --backdrop: #ecebe7;
  }
  * { box-sizing: border-box; margin: 0; padding: 0; }
  html, body { width: 1200px; height: 675px; overflow: hidden; }
  body {
    background: var(--backdrop);
    font-family: "Open Sans", Arial, sans-serif;
    position: relative;
  }
  .card {
    position: absolute;
    top: 188px;
    width: 520px;
    height: 300px;
    border-radius: 16px;
    overflow: hidden;
    box-shadow: 0 6px 18px rgba(0,0,0,0.18);
  }

  /* Back of card */
  .card-back { left: 50px; background: var(--teal); color: var(--paper); }
  .back-headline {
    position: absolute;
    left: 26px; top: 34px;
    font-weight: 800;
    font-size: 54px;
    line-height: 0.92;
    letter-spacing: -1px;
  }
  .back-headline .big { font-size: 66px; }
  .back-divider {
    position: absolute;
    left: 192px; top: 36px;
    width: 2px; height: 226px;
    background: rgba(255,255,255,0.85);
  }
  .jargon-list {
    position: absolute;
    left: 210px; top: 32px;
    list-style: none;
    font-family: "PT Sans Narrow", "Arial Narrow", sans-serif;
    font-size: 29px;
    line-height: 1.27;
    text-transform: uppercase;
  }

  /* Front of card */
  .card-front { left: 630px; background: var(--paper); }
  .front-panel {
    position: absolute;
    left: 236px; top: 0;
    width: 284px; height: 300px;
    background: var(--teal);
  }
  .panel-accent {
    position: absolute;
    right: -40px; top: 50px;
    width: 200px; height: 200px;
    border-radius: 50%;
    background: var(--teal-deep);
  }
  .gold-rule {
    position: absolute;
    left: 230px; top: 150px;
    width: 6px; height: 150px;
    background: var(--gold);
  }
  .brand {
    position: absolute;
    left: 22px; top: 26px;
    display: flex; align-items: center; gap: 10px;
  }
  .brand-mark { width: 24px; height: 24px; background: var(--teal); }
  .brand-name {
    font-weight: 800;
    font-size: 34px;
    color: var(--gold);
    letter-spacing: 1px;
  }
  .contact {
    position: absolute;
    left: 252px; top: 160px;
    color: var(--ink);
  }
  .contact-name {
    font-weight: 800;
    font-size: 17px;
    color: var(--gold);
    letter-spacing: 0.5px;
  }
  .contact-role { font-size: 14px; margin-bottom: 10px; }
  .contact-line {
    display: flex; align-items: center; gap: 8px;
    font-size: 14px; line-height: 1.6;
  }
  .contact-icon {
    width: 16px; height: 16px; flex: none;
    background: var(--gold);
    display: flex; align-items: center; justify-content: center;
  }
  .contact-icon svg { width: 12px; height: 12px; }
</style>
</head>
<body>

<section class="card card-back" aria-label="Back of card">
  <h1 class="back-headline">HOW<br>CAN<br><span class="big">WE</span><br>HELP?</h1>
  <div class="back-divider"></div>
  <ul class="jargon-list">
    <li>Mobile Learning SCORM</li>
    <li>Instructional Design LMS</li>
    <li>MOOCs eLearning HTML5</li>
    <li>Adult Learning Theory</li>
    <li>Gamification Classroom</li>
    <li>xAPI Blended Learning</li>
  </ul>
</section>

<section class="card card-front" aria-label="Front of card">
  <div class="front-panel"><div class="panel-accent"></div></div>
  <div class="gold-rule"></div>

  <div class="brand">
    <span class="brand-mark"></span>
    <span class="brand-name">QVR</span>
  </div>

  <div class="contact">
    <p class="contact-name">MAREN OLVIK</p>
    <p class="contact-role">Managing Director</p>
    <p class="contact-line">
      <span class="contact-icon"><svg viewBox="0 0 12 12"><path d="M2.5 1.5l2 2-1 1.2a6 6 0 0 0 3.8 3.8l1.2-1 2 2-1.2 1.3C5.6 10.8 1.2 6.4 1.2 2.7z" fill="#fff"/></svg></span>
      555-014-2280
    </p>
    <p class="contact-line">
      <span class="contact-icon"><svg viewBox="0 0 12 12"><rect x="1" y="2.5" width="10" height="7" fill="none" stroke="#fff" stroke-width="1.2"/><path d="M1 2.5l5 4 5-4" fill="none" stroke="#fff" stroke-width="1.2"/></svg></span>
      molvik@quorvane.studio
    </p>
    <p class="contact-line">
      <span class="contact-icon"><svg viewBox="0 0 12 12"><circle cx="6" cy="6" r="4.6" fill="none" stroke="#fff" stroke-width="1.1"/><ellipse cx="6" cy="6" rx="2" ry="4.6" fill="none" stroke="#fff" stroke-width="1"/><path d="M1.4 6h9.2" stroke="#fff" stroke-width="1"/></svg></span>
      www.quorvane.studio
    </p>
  </div>
</section>

</body>
</html>
```